Design a Website in Wordpress for an Australian Health Training Company in Health related courses

We require a WORDPRESS based Website (due to add on's we need to use for third party software) to replace our old site.
We offer national face to face delivery in medical reception, terminology and also administration.
The website will have around 6 pages and the ability to describe our main 6 courses (perhaps on the Courses page this may be tabs opening up to details for example?)
I have attached a previous sample of a Joomla site which was being developed (please do not feel you have to copy this - but I am just giving it as a sample - copying would be boring). But it gives an idea of look/feel and colours which may be suitable. Open to other ideas though.
I will provide some of the content, but would like the ability to finish the content myself.
Images and graphics are important. While a few medical photos re great - don't be tempted to us all pictures of doctors and nurses (although a couple would be good) - these are administrative courses so general corporate, eye catching visionary pictures of people in general are great. A medical type picture is also fine.
THE BOOKING system - will be via an ADD ON which will occur at the end of the project and is supplied by a third party software company (our student management system). This project will include up to 2 hours working with the Tech guys from the third party software to enable the ADD ON. If this ADD ON requires more time, we will pay hourly (although I do not expect it will).
Target Market(s)
Mostly a female market, many mature aged women target 25-45 yrs. Mixture of medical/health and corporate. Maybe a bit of mums returning to work and corporate inspiration.
Industry/Entity Type
It Company
Coding
Coded - Design and coding required
Number of Pages Required
5+ page
Requirements
Must have
- Wordpress
- Great graphics
- Interesting
- professional and clean
- Enquiry section (info Pak)
- Should have a University feel to it - Education
- Pages
- Home Page - About Us - Recruitment -Courses - Class Schedule - Traineeships Queensland Funding - Latest News Blog - Corporate Training- Contact us

```html
<!DOCTYPE html>
<html lang="en">
<head>
<meta charset="utf-8">
<title>Harbourline Institute of Training</title>
<link href="https://fonts.googleapis.com/css2?family=Cinzel:wght@400;700&family=Lato:wght@400;700&display=swap" rel="stylesheet">
<style>
:root{
  --blue:#0d4c9b;
  --blue-dark:#083a7a;
  --orange:#f2a23d;
  --dark:#2b2b2b;
  --darker:#1f1f1f;
  --grey-bg:#ebebeb;
  --text:#444;
  --muted:#777;
  --white:#fff;
}
*{box-sizing:border-box;margin:0;padding:0}
html,body{width:1200px;height:3536px;overflow:hidden}
body{font-family:"Lato",Arial,sans-serif;color:var(--text);background:var(--white);position:relative}
.abs{position:absolute}

/* top bar */
.topbar{top:0;left:0;width:1200px;height:36px;background:var(--dark);color:#ddd;font-size:12px}
.topbar .social{left:100px;top:9px;display:flex;gap:8px}
.topbar .social span{width:18px;height:18px;background:var(--blue);border-radius:2px;display:block}
.topbar .contact{left:370px;top:11px;display:flex;gap:22px;align-items:center;white-space:nowrap}
.topbar .contact i{display:inline-block;width:15px;height:15px;background:#fff;border-radius:2px;margin-right:6px;vertical-align:-3px}
.topbar .lang{left:790px;top:0;height:36px;padding:11px 14px;background:#3a3a3a;white-space:nowrap}
.topbar .lang i{display:inline-block;width:16px;height:11px;background:#c33;margin-right:6px;vertical-align:-1px}
.topbar .auth{left:935px;top:11px;letter-spacing:1px;white-space:nowrap}

/* header */
.header{top:36px;left:0;width:1200px;height:98px;background:var(--white)}
.brand{left:100px;top:14px;display:flex;align-items:center;gap:10px}
.brand .mark{width:62px;height:62px;border-radius:50%;background:var(--blue)}
.brand .name{font-weight:700;font-size:13px;color:var(--blue);line-height:1.25;text-transform:uppercase;width:110px}
.mainnav{right:100px;top:40px;display:flex;gap:40px;font-family:"Cinzel",Georgia,serif;font-size:14px;color:#333;letter-spacing:1px}
.subnav{top:134px;left:0;width:1200px;height:40px;background:var(--blue);border-bottom:3px solid var(--blue-dark)}
.subnav ul{list-style:none;display:flex;gap:62px;position:absolute;left:100px;top:12px;font-family:"Cinzel",Georgia,serif;font-size:13px;color:#fff;letter-spacing:1px}
.subnav .search{position:absolute;right:100px;top:0;width:40px;height:40px;background:var(--orange)}

/* hero */
.hero{top:174px;left:0;width:1200px;height:514px;background:linear-gradient(100deg,#6e86a8 0%,#c9d4e2 35%,#e8e3df 55%,#b9c6d8 80%,#6a7f9e 100%)}
.hero-caption{left:0;top:562px;width:566px;height:126px;background:rgba(20,20,20,.7);padding:20px 0 0 100px;color:#fff}
.hero-caption h2{font-family:"Cinzel",Georgia,serif;font-weight:400;font-size:25px;letter-spacing:1px;margin-bottom:8px}
.hero-caption p{font-size:13px;line-height:1.5;width:450px}
.hero-arrows{right:100px;top:650px;color:#fff;font-size:26px;letter-spacing:14px}

/* section titles */
.section-title{width:1200px;text-align:center;font-family:"Cinzel",Georgia,serif;font-size:33px;color:#222;letter-spacing:1px}
.section-title em{font-style:normal;color:var(--orange)}
.section-title::after{content:"";display:block;width:210px;height:1px;background:#bbb;margin:8px auto 0}

/* about */
.about-text{top:796px;left:120px;width:960px;text-align:center;font-size:13px;line-height:1.7;color:var(--text)}
.feature{top:880px;width:300px;display:flex;gap:16px}
.feature .ico{width:92px;height:92px;border-radius:50%;background:var(--blue);border:5px solid #dde6f2;flex:none;display:flex;align-items:center;justify-content:center}
.feature h4{font-family:"Cinzel",Georgia,serif;font-size:19px;color:#222;margin:4px 0 6px}
.feature p{font-size:13px;line-height:1.55}

/* courses */
.courses{top:1030px;left:0;width:1200px;height:530px;background:var(--grey-bg)}
.course{top:108px;width:316px}
.course .photo{width:316px;height:252px;border:5px solid var(--blue);background:linear-gradient(135deg,#d7dde6,#8fa3bf)}
.course h3{font-family:"Cinzel",Georgia,serif;font-weight:400;font-size:19px;color:var(--blue);text-align:center;line-height:1.3;margin-top:22px;height:56px;letter-spacing:1px}
.course .btn{display:block;width:118px;height:36px;margin:20px auto 0;background:var(--blue);color:#fff;font-size:13px;text-align:center;line-height:36px}
.courses .chev{top:212px}

/* candidate / employer */
.split{top:1560px;left:0;width:1200px;height:338px}
.split .left{left:0;top:0;width:600px;height:338px;background:linear-gradient(90deg,#123f7e,#2e6bb5)}
.split .right{left:600px;top:0;width:600px;height:338px;background:linear-gradient(90deg,#e89a3b,#f3b469)}
.split h3{font-family:"Cinzel",Georgia,serif;font-weight:400;font-size:28px;color:#fff;letter-spacing:1px}
.split p{font-size:13px;color:#fff;line-height:1.6}
.split .outline{display:inline-block;border:2px solid #fff;color:#fff;font-size:14px;padding:8px 16px}
.split .badge{left:488px;top:50px;width:224px;height:224px;border-radius:50%;background:#fff;border:8px solid #f1f1f1}

/* why choose */
.why-item{width:480px}
.why-item .ico{position:absolute;left:-80px;top:-6px;width:66px;height:66px;border-radius:50%;background:var(--blue);border:4px solid #dfe6ef;display:flex;align-items:center;justify-content:center}
.why-item h4{font-size:17px;color:var(--blue);font-weight:700;margin-bottom:4px}
.why-item p{font-size:14px;line-height:1.45;color:#333}
.why-brand{left:110px;top:2170px;width:300px;text-align:center}
.why-brand .name{font-weight:700;font-size:24px;color:var(--blue);line-height:1.15;text-transform:uppercase}
.why-brand .mark{width:150px;height:150px;background:var(--blue);margin:20px auto 0}

/* cta */
.cta{top:2628px;left:0;width:1200px;height:177px;background:linear-gradient(90deg,#2a2f36,#3d444d 60%,#2a2f36)}
.cta p{position:absolute;left:100px;top:58px;font-size:22px;font-weight:700;color:#fff;line-height:1.45}
.cta .book{position:absolute;left:959px;top:58px;width:142px;height:56px;background:var(--orange);color:#222;font-weight:700;font-size:17px;text-align:center;line-height:56px}

/* testimonials */
.avatars{top:2908px;left:0;width:1200px;display:flex;justify-content:center;gap:40px}
.avatars span{width:90px;height:90px;border-radius:50%;background:linear-gradient(135deg,#e6d1c2,#a98c7a);border:4px solid #fff;box-shadow:0 0 0 2px #ccc}
.quote{top:3020px;left:80px;width:1040px;text-align:center;font-size:13.5px;font-style:italic;line-height:2;color:#444}

/* footer */
.footer{top:3154px;left:0;width:1200px;height:346px;background:var(--blue)}
.footer .dark{position:absolute;left:0;top:0;height:346px;width:480px;background:var(--darker);clip-path:polygon(0 0,100% 0,440px 100%,0 100%)}
.footer h5{font-family:"Cinzel",Georgia,serif;font-weight:400;font-size:22px;color:#fff;letter-spacing:1px}
.footer h5::after{content:"";display:block;width:60px;height:2px;background:#fff;margin-top:8px;opacity:.6}
.field{width:315px;height:32px;background:#3c3c3c;color:#aaa;font-size:13px;padding:8px 10px;margin-bottom:10px}
.submit{width:110px;height:36px;background:#f4f4f4;color:#222;font-weight:700;font-size:14px;text-align:center;line-height:36px;border-radius:2px}
.links{font-size:13px;color:#fff;line-height:35px;list-style:none}
.links li::before{content:"\203A";margin-right:10px}
.contact-list{font-size:13px;color:#fff;line-height:1.5}
.contact-list i{position:absolute;left:0;width:20px;height:20px;border-radius:3px;background:#fff}
.fsocial{display:flex;gap:8px}
.fsocial span{width:32px;height:32px;border-radius:50%;background:#fff;display:block}
.copyright{top:3500px;left:0;width:1200px;height:36px;background:var(--darker);color:#ccc;font-size:12px;text-align:center;line-height:36px}
</style>
</head>
<body>

<!-- top bar -->
<div class="topbar abs">
  <div class="social abs"><span></span><span></span><span></span><span></span></div>
  <div class="contact abs"><span><i></i>+61 (07) 5550 1842</span><span><i></i>INFO@HARBOURLINE-EXAMPLE.COM</span></div>
  <div class="lang abs"><i></i>ENGLISH ▾</div>
  <div class="auth abs">LOG IN &nbsp;/&nbsp; REGISTER</div>
</div>

<!-- header -->
<header class="header abs">
  <div class="brand abs"><span class="mark"></span><span class="name">Harbourline Institute of Training</span></div>
  <nav class="mainnav abs"><span>HOME</span><span>ABOUT US</span><span>COURSES</span><span>RECRUITMENT</span><span>CLASS SCHEDULE</span></nav>
</header>
<nav class="subnav abs">
  <ul><li>TRAINEESHIPS QUEENSLAND FUNDING</li><li>LATEST NEWS BLOG</li><li>CORPORATE TRAINING</li><li>CONTACT US</li></ul>
  <div class="search">
    <svg width="40" height="40" viewBox="0 0 40 40"><circle cx="18" cy="18" r="6" fill="none" stroke="#fff" stroke-width="2"/><line x1="22" y1="22" x2="27" y2="27" stroke="#fff" stroke-width="2"/></svg>
  </div>
</nav>

<!-- hero -->
<section class="hero abs" role="img" aria-label="Photo of smiling healthcare and office staff at a training session"></section>
<div class="hero-caption abs">
  <h2>Courses for Busy People</h2>
  <p>Our unique quickFASTTM (Combined Assessment &amp; Training) class format delivers accelerated training that's specifically targeted at busy profes-sionals....</p>
</div>
<div class="hero-arrows abs">‹›</div>

<!-- about -->
<h2 class="section-title abs" style="top:726px"><em>About</em> Us</h2>
<p class="about-text abs">Harbourline is Australia's Leading Provider of Educational, Training and Support Services for the Medical and Dental industry - enabling students to be immediately skilled and 'Job Ready' for a career in Health. Harbourline is a Registered Training Organisation offering specialised Medical Administration Training in over 15 locations Australia wide.... [ + ]</p>

<div class="feature abs" style="left:100px">
  <div class="ico"><svg width="44" height="36" viewBox="0 0 44 36"><path d="M22 6 C14 1 6 2 2 4 V32 C6 30 14 29 22 34 C30 29 38 30 42 32 V4 C38 2 30 1 22 6 Z M22 6 V34" fill="none" stroke="#fff" stroke-width="3"/></svg></div>
  <div><h4>Story</h4><p>Harbourline Health Management started business in February 1999 primarily..... [ + ]</p></div>
</div>
<div class="feature abs" style="left:465px">
  <div class="ico"><svg width="46" height="30" viewBox="0 0 46 30"><path d="M2 15 C12 0 34 0 44 15 C34 30 12 30 2 15 Z" fill="none" stroke="#fff" stroke-width="3"/><circle cx="23" cy="15" r="7" fill="#fff"/></svg></div>
  <div><h4>Vision</h4><p>To be Australia's Leading Educational supplier in our Core Units..... [ + ]</p></div>
</div>
<div class="feature abs" style="left:800px">
  <div class="ico"><svg width="46" height="32" viewBox="0 0 46 32"><path d="M2 10 L12 4 L22 10 L34 4 L44 10 M8 14 L20 26 Q23 29 26 26 L38 14" fill="none" stroke="#fff" stroke-width="3" stroke-linejoin="round"/></svg></div>
  <div><h4>Core Values</h4><p>The Harbourline business is always evolving and as we do, we aim to be true .... [ + ]</p></div>
</div>

<!-- courses -->
<section class="courses abs">
  <h2 class="section-title abs" style="top:38px"><em>Our</em> Courses</h2>
  <svg class="chev abs" style="left:32px" width="30" height="60" viewBox="0 0 30 60"><polyline points="26,2 4,30 26,58" fill="none" stroke="#999" stroke-width="2"/></svg>
  <svg class="chev abs" style="left:1138px" width="30" height="60" viewBox="0 0 30 60"><polyline points="4,2 26,30 4,58" fill="none" stroke="#999" stroke-width="2"/></svg>

  <div class="course abs" style="left:99px">
    <div class="photo" role="img" aria-label="Photo of reception staff working at computers"></div>
    <h3>Medical Reception<br>&amp; Terminology</h3>
    <span class="btn">Read More</span>
  </div>
  <div class="course abs" style="left:443px">
    <div class="photo" role="img" aria-label="Photo of a smiling business team"></div>
    <h3>Cert III Business<br>Administration</h3>
    <span class="btn">Read More</span>
  </div>
  <div class="course abs" style="left:785px">
    <div class="photo" style="background:linear-gradient(135deg,#efe6d2,#c98d7a)" role="img" aria-label="Photo of a medical terminology book with a stethoscope"></div>
    <h3>Medical<br>Terminology</h3>
    <span class="btn">Read More</span>
  </div>
</section>

<!-- candidate / employer -->
<section class="split abs">
  <div class="left abs" role="img" aria-label="Blue-tinted photo of a candidate in a meeting">
    <div class="abs" style="left:100px;top:60px;width:380px">
      <h3>For the Candidate</h3>
      <p style="margin-top:14px"><b>Looking for a Career in Medical Administration?</b><br>Our partner company, Harbourline Institute of Training has been the market leader in Medical Reception Training in Australia for over 17 years. In fact, we pioneered.</p>
      <span class="outline" style="margin-top:20px">Read More</span>
    </div>
  </div>
  <div class="right abs" role="img" aria-label="Orange-tinted photo of an employer at a desk">
    <div class="abs" style="left:140px;top:60px;width:360px">
      <h3>For the Employer</h3>
      <p style="margin-top:14px">Harbourline Recruitment is a leading National Health Specialist Recruitment Agency with expertise in Medical and Dental administrative recruitment for both permanent and temporary staff.</p>
      <span class="outline" style="margin-top:20px">Read More</span>
    </div>
  </div>
  <div class="badge abs" style="display:flex;align-items:center;justify-content:center;text-align:center">
    <span style="font-weight:700;font-size:16px;color:var(--blue);text-transform:uppercase;line-height:1.2">Harbourline<br>Institute<br>of Training</span>
  </div>
</section>

<!-- why choose -->
<h2 class="section-title abs" style="top:1932px"><em>Why Choose</em> Us</h2>

<svg class="abs" style="left:0;top:1990px" width="700" height="620" viewBox="0 0 700 620">
  <path d="M280 40 A300 270 0 0 1 280 580" fill="none" stroke="#9a9a9a" stroke-width="8"/>
  <g fill="#fff" stroke="#888" stroke-width="3">
    <circle cx="300" cy="44" r="9"/><circle cx="393" cy="106" r="9"/><circle cx="472" cy="215" r="9"/>
    <circle cx="472" cy="405" r="9"/><circle cx="393" cy="515" r="9"/><circle cx="300" cy="576" r="9"/>
  </g>
  <g stroke="#bbb" stroke-width="1.5">
    <line x1="309" y1="44" x2="450" y2="30"/><line x1="402" y1="106" x2="540" y2="170"/>
    <line x1="481" y1="215" x2="600" y2="290"/><line x1="481" y1="405" x2="530" y2="420"/>
    <line x1="402" y1="515" x2="480" y2="540"/>
  </g>
</svg>

<div class="why-brand abs">
  <div class="name">Harbourline Institute<br>of Training</div>
  <div class="mark"></div>
</div>

<div class="why-item abs" style="left:552px;top:2010px">
  <div class="ico"><svg width="30" height="34" viewBox="0 0 30 34"><circle cx="15" cy="12" r="10" fill="none" stroke="#fff" stroke-width="3"/><path d="M8 20 L5 33 L15 28 L25 33 L22 20" fill="#fff"/></svg></div>
  <h4>Quality</h4>
  <p>Harbourline delivery quality, effective training facilitated by industry leaders.<br>Just ask our students who rate us on average of 4.7 out of 5.</p>
</div>
<div class="why-item abs" style="left:642px;top:2120px">
  <div class="ico"><svg width="32" height="32" viewBox="0 0 32 32"><path d="M4 28 L16 16 M12 4 L14 10 L20 10 L15 14 L17 20 L12 16 L7 20 L9 14 L4 10 L10 10 Z" fill="#fff" stroke="#fff" stroke-width="2"/></svg></div>
  <h4>Experience</h4>
  <p>Harbourline is Australia's largest and leading providers of nationally recognised training in health administration – training from over 17 locations Australia wide.</p>
</div>
<div class="why-item abs" style="left:698px;top:2250px">
  <div class="ico"><svg width="32" height="30" viewBox="0 0 32 30"><rect x="3" y="18" width="6" height="10" fill="#fff"/><rect x="13" y="12" width="6" height="16" fill="#fff"/><rect x="23" y="5" width="6" height="23" fill="#fff"/></svg></div>
  <h4>Value</h4>
  <p>Our innovative teaching approach allows us to deliver<br>exceptional training at affordable prices with no hidden extras.</p>
</div>
<div class="why-item abs" style="left:634px;top:2375px">
  <div class="ico"><svg width="34" height="34" viewBox="0 0 34 34"><circle cx="13" cy="14" r="8" fill="none" stroke="#fff" stroke-width="4" stroke-dasharray="4 2.3"/><circle cx="13" cy="14" r="3" fill="#fff"/><circle cx="25" cy="25" r="5" fill="none" stroke="#fff" stroke-width="3" stroke-dasharray="3 1.7"/></svg></div>
  <h4>Industry Recognised</h4>
  <p>Harbourline work hand in hand with industry to develop our core programme and consolidate the programme annually to keep the programme fresh and relevant.</p>
</div>
<div class="why-item abs" style="left:587px;top:2500px">
  <div class="ico"><svg width="32" height="32" viewBox="0 0 32 32"><rect x="4" y="4" width="24" height="17" fill="none" stroke="#fff" stroke-width="3"/><line x1="16" y1="21" x2="16" y2="29" stroke="#fff" stroke-width="3"/><polyline points="8,17 13,11 17,14 23,8" fill="none" stroke="#fff" stroke-width="2"/></svg></div>
  <h4>Great Job Results</h4>
  <p>Harbourline students get jobs! &nbsp;Our focus is to create job-ready students who are mentored to achieve their goals. &nbsp;Harbourline also provide a recruitment service for industry and graduates.</p>
</div>

<!-- call to action -->
<section class="cta abs" role="img" aria-label="Dark photo background of people studying">
  <p>Enrol In Our BSB51915 Diploma Of Liadership And Managemenr<br>And Gain Vaaluable Skills To Launch Your Management Career.</p>
  <span class="book">Booking Now</span>
</section>

<!-- testimonials -->
<h2 class="section-title abs" style="top:2838px"><em>Clients</em> Testimonials</h2>
<svg class="abs" style="left:306px;top:2935px" width="20" height="40" viewBox="0 0 20 40"><polyline points="16,2 4,20 16,38" fill="none" stroke="#bbb" stroke-width="2"/></svg>
<svg class="abs" style="left:872px;top:2935px" width="20" height="40" viewBox="0 0 20 40"><polyline points="4,2 16,20 4,38" fill="none" stroke="#bbb" stroke-width="2"/></svg>
<div class="avatars abs">
  <span role="img" aria-label="Client portrait"></span>
  <span role="img" aria-label="Client portrait"></span>
  <span role="img" aria-label="Client portrait"></span>
  <span role="img" aria-label="Client portrait"></span>
</div>
<p class="quote abs"><span style="color:#ccc;font-size:26px;font-style:normal;line-height:0">“</span> I completed the course on Feb 13th. Loved it. The trainers, Maren and Tess were excellent in their delivery and knowledge. I want to say a huge thank you for the course and knowledge I came away with.I have secured a fantastic job after my first application! Such good value for money too! I would highly recommend it.I'm a mature age person so it's never too late to up-skill yourself to get what you deserve! <span style="color:#ccc;font-size:26px;font-style:normal;line-height:0">”</span></p>

<!-- footer -->
<footer class="footer abs">
  <div class="dark"></div>
  <div class="abs" style="left:100px;top:36px">
    <h5>EMAIL me an Info Pack</h5>
    <div style="margin-top:22px">
      <div class="field">Name</div>
      <div class="field">Email</div>
      <div class="field">Course</div>
      <div class="field" style="height:72px">State</div>
      <div class="submit" style="margin-top:14px">Submit</div>
    </div>
  </div>
  <div class="abs" style="left:490px;top:36px">
    <h5>Quick Links</h5>
    <div style="display:flex;gap:46px;margin-top:14px">
      <ul class="links"><li>Home</li><li>About Us</li><li>Courses</li><li>Recruitment</li><li>Class Schedule</li><li>Traineeships Queensland Funding</li></ul>
      <ul class="links" style="margin-left:-150px"><li>Latest News Blog</li><li>Corporate Training</li><li>Contact Us</li></ul>
    </div>
  </div>
  <div class="abs" style="left:858px;top:36px;width:250px">
    <h5>Contact Us</h5>
    <div class="contact-list abs" style="top:70px;padding-left:36px;width:250px"><i style="top:2px"></i><b>Harbourline Health Trainings</b><br>123, Ut wisi enim ad minim ve, Mor nostrni tation -123 456</div>
    <div class="contact-list abs" style="top:150px;padding-left:36px;width:250px"><i style="top:0"></i>+61 (07) 5550 1842</div>
    <div class="contact-list abs" style="top:208px;padding-left:36px;width:250px"><i style="top:0"></i>info@harbourline-example.com</div>
    <div class="fsocial abs" style="top:256px;left:22px"><span></span><span></span><span></span><span></span></div>
  </div>
</footer>
<div class="copyright abs">Copyright © 2016 Harbourline Health Trainings. All Right Reserved</div>

</body>
</html>
```